W. Darrow Billboard

2 miles ahead on right
Voted number 1 ... again!
California cuisine
Located in Historic Marbury Hill Inn
Picture of a couple dining
www.torvellis.com 555.317.2968

Target Market(s)

travelers

Industry/Entity Type

hospitality

Font styles to use
Serif

Colors
59FF00
82FF00
B8FF75
E3FFCB
F4FFEA
EE7325
F08F49
F5BC92
FAE3D3
FDF4ED

Requirements
Should not have
• bright colors

```html
<!DOCTYPE html>
<html lang="en">
<head>
<meta charset="utf-8">
<title>W. Darrow Billboard</title>
<link rel="stylesheet" href="https://fonts.googleapis.com/css2?family=Ultra&family=Playfair+Display:wght@700&family=Open+Sans:wght@400&display=swap">
<style>
  :root {
    --page: #e9eef3;
    --board: #ffffff;
    --brand-orange: #e8461c;
    --green-dark: #4f9d12;
    --green: #6cc51a;
    --green-light: #9ddd45;
    --ink: #2d2d2d;
    --badge-red: #b5161b;
    --badge-gold: #d9a93a;
    --photo-light: #f4f4f2;
    --photo-mid: #d9d9d6;
  }
  * { box-sizing: border-box; margin: 0; padding: 0; }
  html, body { width: 1200px; height: 800px; overflow: hidden; background: var(--page); }
  .billboard {
    position: absolute; left: 20px; top: 110px; width: 1160px; height: 580px;
    background: var(--board); overflow: hidden;
    box-shadow: 0 4px 18px rgba(0,0,0,.12);
  }
  .brand { position: absolute; left: 40px; top: 18px; color: var(--brand-orange); font-family: "Ultra", serif; }
  .brand-name { font-size: 128px; line-height: 1; letter-spacing: 1px; }
  .brand-sub { font-size: 30px; letter-spacing: 6px; margin: 4px 0 0 150px; text-transform: uppercase; }
  .brand-dot {
    position: absolute; left: 700px; top: 40px; width: 64px; height: 64px;
    border-radius: 50%; background: var(--green-light);
  }
  .tagline {
    position: absolute; left: 60px; top: 238px;
    font-family: "Playfair Display", serif; font-weight: 700; font-size: 50px;
    color: var(--green); letter-spacing: 1px;
  }
  .cuisine-pill {
    position: absolute; left: 34px; top: 318px; width: 540px; height: 74px;
    border-radius: 37px;
    background: linear-gradient(180deg, var(--green-light), var(--green) 55%, var(--green-dark));
    display: flex; align-items: center; justify-content: center;
    font-family: "Ultra", serif; font-size: 40px; color: #fff; letter-spacing: 2px;
    text-shadow: 0 2px 0 rgba(0,0,0,.35);
  }
  .location {
    position: absolute; left: 170px; top: 414px;
    font-family: "Open Sans", sans-serif; font-size: 30px; color: var(--ink);
  }
  .phone-band {
    position: absolute; left: 0; top: 505px; width: 430px; height: 75px;
    border-radius: 0 38px 0 0; background: var(--green);
    display: flex; align-items: center; padding-left: 22px;
    font-family: "Ultra", serif; font-size: 40px; color: #fff; letter-spacing: 1px;
  }
  .base-line { position: absolute; left: 420px; top: 570px; width: 380px; height: 10px; background: var(--green); }
  .award { position: absolute; left: 560px; top: 300px; width: 200px; height: 250px; }
  .photo-frame { position: absolute; left: 770px; top: 0; width: 390px; height: 580px; }
</style>
</head>
<body>
  <main class="billboard">
    <div class="brand-dot" aria-hidden="true"></div>
    <div class="brand">
      <div class="brand-name">Torvelli's</div>
      <div class="brand-sub">Southwest Bar &amp; Grill</div>
    </div>

    <p class="tagline">Good Food, Good Life</p>
    <div class="cuisine-pill">California Cuisine</div>
    <p class="location">Historic Marbury Hill Inn</p>

    <div class="phone-band">555.317.2968</div>
    <div class="base-line" aria-hidden="true"></div>

    <svg class="award" viewBox="0 0 200 250" aria-label="Voted number 1 again">
      <defs>
        <path id="award-arc" d="M30 108 A72 72 0 0 1 172 100"/>
      </defs>
      <text font-family="Playfair Display, serif" font-weight="700" font-size="22" fill="#2d2d2d">
        <textPath href="#award-arc">Voted Number</textPath>
      </text>
      <polygon points="62,170 90,175 72,240 58,214 38,224" fill="var(--badge-gold)"/>
      <polygon points="138,170 110,175 128,240 142,214 162,224" fill="var(--badge-gold)"/>
      <circle cx="100" cy="140" r="64" fill="var(--badge-gold)"/>
      <circle cx="100" cy="140" r="54" fill="var(--badge-red)"/>
      <text x="100" y="150" text-anchor="middle" font-family="Ultra, serif" font-size="62" fill="var(--badge-gold)">1</text>
      <text x="100" y="178" text-anchor="middle" font-family="Playfair Display, serif" font-weight="700" font-size="20" fill="#fff">again!</text>
    </svg>

    <svg class="photo-frame" viewBox="0 0 390 580">
      <defs>
        <linearGradient id="photo-tone" x1="0" y1="0" x2="1" y2="1">
          <stop offset="0" stop-color="var(--photo-light)"/>
          <stop offset="1" stop-color="var(--photo-mid)"/>
        </linearGradient>
      </defs>
      <path d="M90 0 H390 V580 H120 C70 430 40 260 60 120 C66 70 76 30 90 0 Z"
            fill="url(#photo-tone)" role="img" aria-label="Photo of a couple dining at a white-clothed table"/>
      <path d="M90 0 C76 30 66 70 60 120 C40 260 70 430 120 580"
            fill="none" stroke="var(--green)" stroke-width="12"/>
    </svg>
  </main>
</body>
</html>
```